DESKHAVEN COSPACE Website design and coding

DESKHAVEN COSPACE

DESKHAVEN is Port Halden’s first (and currently only) shared business co-working space. We share the same upscale, casual work environment, but we work independently on our own (or our team’s) projects and goals. For only a flat $195 membership fee per month, you have your very own all-inclusive, fun, personal business office environment. Website is written (Word file #12, below); and all pictures etc provided. Port Halden is a beachy, coastal, historic city an hour from Houston, Texas USA. Logo (file 11 below) is temporary only.

Target Market(s)

Outside sales people, medical students looking for study hall, Houston companies looking for local office, real estate agents, graphic artists, entrepreneurs, etc

Contact Information for Business Card

will discuss --want to combine with current business card with multiple businesses

Logo Text

DESKHAVEN COSPACE

Coding

Coded - Design and coding required

Number of Pages Required

5+ page

Colors
ec1f27
fbed22

Requirements
Nice to have
• maroon/wine dominant with yellow and red accents, gray base are the colors of the space--website could coordinate--but open to creative ideas/combinations

```html
<!DOCTYPE html>
<html lang="en">
<head>
<meta charset="utf-8">
<title>DESKHAVEN COSPACE — Membership</title>
<link href="https://fonts.googleapis.com/css2?family=Catamaran:wght@400;500;600;700;800&family=Josefin+Sans:wght@700&family=Roboto:wght@400;500&display=swap" rel="stylesheet">
<style>
:root{
  --maroon:#850000;
  --yellow:#fcd600;
  --light:#f3f3f3;
  --gray:#e6e6e6;
  --ink:#2b2b2b;
  --field:#fdf9e2;
  --border:#e2e2e2;
  --muted:#8c8c8c;
}
*{margin:0;padding:0;box-sizing:border-box}
html,body{width:1200px;height:1200px;overflow:hidden;background:#fff}
.canvas{position:relative;width:1200px;height:1200px;background:#fff;font-family:'Catamaran',sans-serif}
.abs{position:absolute}
.site{position:absolute;left:0;top:0;width:589px;height:1200px;background:var(--light)}
.nav{position:absolute;left:0;top:0;width:589px;height:27px;background:var(--maroon)}
.brand{position:absolute;left:55px;top:7px;font-size:9px;color:var(--yellow);letter-spacing:.2px}
.brand b{font-weight:800}
.brand span{font-weight:400}
.nav-links{position:absolute;top:8px;font-size:6.5px;color:#fff}
.nav-links.active{color:var(--yellow)}
.nav-links.active::after{content:"";position:absolute;left:0;right:0;bottom:-4px;height:1px;background:var(--yellow)}
.hero{position:absolute;left:0;top:27px;width:589px;height:160px;background:linear-gradient(120deg,#3a2e24,#5a4a3c 45%,#2c241d)}
.hero-title{position:absolute;left:0;width:589px;text-align:center;color:#fff;font-size:21px;font-weight:700}
.crumb{position:absolute;left:0;width:589px;text-align:center;color:#fff;font-size:6.5px}
.crumb span{color:var(--yellow)}
.sec-title{position:absolute;left:0;width:580px;top:240px;text-align:center;font-size:21px;color:var(--maroon)}
.sec-title b{font-weight:800}
.rule{position:absolute;height:2px;background:var(--yellow)}
.intro{position:absolute;left:165px;width:259px;top:290px;text-align:center;font-size:6px;line-height:10.4px;color:var(--ink)}
.price-card{position:absolute;left:92px;top:375px;width:133px;height:245px;background:var(--maroon);color:#fff;box-shadow:0 2px 6px rgba(0,0,0,.25)}
.price{position:absolute;left:0;width:133px;top:16px;text-align:center;font-size:16px;font-weight:700}
.amen-head{position:absolute;left:0;width:133px;top:51px;text-align:center;font-size:6.6px;font-weight:700;letter-spacing:.3px}
.amen{position:absolute;left:23px;font-size:6.2px}
.amen svg{position:absolute;left:-1px;top:0}
.amen span{position:absolute;left:12px;top:0;white-space:nowrap}
.amen-note{position:absolute;left:0;width:133px;top:175px;text-align:center;font-size:6px;line-height:9.5px}
.btn-yellow{position:absolute;background:var(--yellow);color:#111;font-weight:700;font-size:6.5px;text-align:center;border-radius:12px}
.photo{position:absolute}
.frame{position:absolute;left:297px;top:401px;width:191px;height:216px;border:4px solid var(--yellow)}
.band{position:absolute;left:0;top:669px;width:589px;height:346px;background:var(--gray)}
.cta-title{position:absolute;left:391px;top:700px;font-size:20px;line-height:26px;color:var(--maroon)}
.cta-title b{font-weight:800}
.cta-text{position:absolute;left:391px;top:772px;width:145px;font-size:6px;line-height:10.4px;color:var(--ink)}
.footer{position:absolute;left:0;top:1015px;width:589px;height:185px;background:var(--maroon);color:#fff}
.f-brand{position:absolute;left:55px;top:29px;font-size:11px;line-height:10px;color:var(--yellow)}
.f-brand b{font-weight:800}
.f-tag{position:absolute;left:55px;top:64px;font-size:6.2px;line-height:11.7px}
.f-copy{position:absolute;left:58px;top:113px;font-size:3.6px;line-height:8px}
.f-copy span{color:var(--yellow)}
.f-head{position:absolute;top:30px;font-size:7.5px;font-weight:700;color:var(--yellow)}
.f-head::after{content:"";position:absolute;left:0;top:14px;width:43px;height:1.5px;background:var(--yellow)}
.f-list{position:absolute;top:64px;font-size:6.2px;line-height:11.7px;list-style:none}
.f-list .hl{color:var(--yellow)}
.portal-title{position:absolute;left:736px;width:464px;top:167px;text-align:center;font-family:'Josefin Sans',sans-serif;font-weight:700;font-size:20px;letter-spacing:2.2px;color:#111}
.hair{position:absolute;height:1px;background:#ececec}
.portal{font-family:'Roboto',sans-serif;color:#333}
.pay-btn{position:absolute;left:754px;top:213px;width:416px;height:47px;background:#000;border-radius:4px;color:#fff;font-size:22px;font-weight:500;text-align:center;line-height:47px}
.or{position:absolute;left:754px;width:416px;top:296px;text-align:center;font-size:15px;color:#999}
.label{position:absolute;left:754px;font-size:14px;color:#555}
.box{position:absolute;left:754px;width:417px;border:1px solid var(--border);border-radius:5px;overflow:hidden;box-shadow:0 1px 2px rgba(0,0,0,.08)}
.cell{position:absolute;height:40px;font-size:15.5px;line-height:39px;padding-left:13px;color:#333;border-bottom:1px solid var(--border)}
.cell.fill{background:var(--field)}
.cell .aside{position:absolute;right:18px;top:0;color:#9a9a9a;font-size:14px}
.chev{position:absolute;right:18px;top:14px}
.subscribe{position:absolute;left:754px;top:892px;width:417px;height:47px;background:var(--maroon);border-radius:5px;color:#fff;font-size:17px;font-weight:500;text-align:center;line-height:47px;box-shadow:0 1px 3px rgba(0,0,0,.3)}
.fine{position:absolute;left:748px;width:430px;top:957px;text-align:center;font-size:13.5px;line-height:18.6px;color:#8a8a8a}
.card-tag{position:absolute;right:12px;top:11px;font-size:9px;font-weight:500;color:#1a1f71;border:1px solid #ddd;border-radius:2px;padding:0 3px;line-height:14px}
</style>
</head>
<body>
<div class="canvas">

  <div class="site">
    <header class="nav">
      <div class="brand"><b>DESKHAVEN</b> <span>COSPACE</span></div>
      <div class="nav-links" style="left:335px">Home</div>
      <div class="nav-links" style="left:370px">About</div>
      <div class="nav-links" style="left:406px">Amenities</div>
      <div class="nav-links active" style="left:455px">Membership</div>
      <div class="nav-links" style="left:510px">Contact</div>
    </header>

    <section class="hero" role="img" aria-label="Photo of coworkers shaking hands around a meeting table">
      <div class="hero-title" style="top:57px">Membership</div>
      <div class="crumb" style="top:95px"><span>Home</span> → Membership</div>
    </section>

    <h2 class="sec-title"><b>Deskhaven</b> Membership</h2>
    <div class="rule" style="left:268px;top:276px;width:43px"></div>
    <p class="intro">For only $195 a month, charged to your credit card, you get the all-inclusive amenities for one flat fee. The only “extras” are for copies, on a per-copy basis. We will bill you automatically monthly on the first of the month unless you cancel. You need only give us thirty day notice to cancel (but no partial month refunds can be given).</p>

    <div class="price-card">
      <div class="price">$195/month</div>
      <div class="rule" style="left:42px;top:42px;width:43px;height:1.5px"></div>
      <div class="amen-head">ALL-INCLUSIVE AMENITIES</div>
      <div class="amen" style="top:70px"><svg width="7" height="7" viewBox="0 0 8 8"><circle cx="4" cy="4" r="4" fill="#fcd600"/><path d="M2.2 4.1l1.2 1.2 2.4-2.5" stroke="#850000" stroke-width="1" fill="none"/></svg><span>24-hr. access</span></div>
      <div class="amen" style="top:85px"><svg width="7" height="7" viewBox="0 0 8 8"><circle cx="4" cy="4" r="4" fill="#fcd600"/><path d="M2.2 4.1l1.2 1.2 2.4-2.5" stroke="#850000" stroke-width="1" fill="none"/></svg><span>Keyless digital door entry</span></div>
      <div class="amen" style="top:100px"><svg width="7" height="7" viewBox="0 0 8 8"><circle cx="4" cy="4" r="4" fill="#fcd600"/><path d="M2.2 4.1l1.2 1.2 2.4-2.5" stroke="#850000" stroke-width="1" fill="none"/></svg><span>FREE Wi-fi</span></div>
      <div class="amen" style="top:114px"><svg width="7" height="7" viewBox="0 0 8 8"><circle cx="4" cy="4" r="4" fill="#fcd600"/><path d="M2.2 4.1l1.2 1.2 2.4-2.5" stroke="#850000" stroke-width="1" fill="none"/></svg><span>Use of conference room</span></div>
      <div class="amen" style="top:129px"><svg width="7" height="7" viewBox="0 0 8 8"><circle cx="4" cy="4" r="4" fill="#fcd600"/><path d="M2.2 4.1l1.2 1.2 2.4-2.5" stroke="#850000" stroke-width="1" fill="none"/></svg><span>Office use</span></div>
      <div class="amen" style="top:144px"><svg width="7" height="7" viewBox="0 0 8 8"><circle cx="4" cy="4" r="4" fill="#fcd600"/><path d="M2.2 4.1l1.2 1.2 2.4-2.5" stroke="#850000" stroke-width="1" fill="none"/></svg><span>Use of the kitchen</span></div>
      <div class="amen" style="top:158px"><svg width="7" height="7" viewBox="0 0 8 8"><circle cx="4" cy="4" r="4" fill="#fcd600"/><path d="M2.2 4.1l1.2 1.2 2.4-2.5" stroke="#850000" stroke-width="1" fill="none"/></svg><span>Lockers</span></div>
      <div class="amen-note">All other amenities included<br>(at no additional cost)</div>
      <div class="btn-yellow" style="left:33px;top:206px;width:66px;height:20px;line-height:20px">Join Now</div>
    </div>

    <div class="frame"></div>
    <div class="photo" style="left:314px;top:377px;width:192px;height:217px;background:linear-gradient(135deg,#e9e2d8,#c9b39a 55%,#8d7560)" role="img" aria-label="Photo of a smiling member working at a laptop"></div>

    <section class="band">
      <div class="photo" style="left:55px;top:32px;width:315px;height:165px;background:linear-gradient(160deg,#cfcfcf,#6f6a5f 50%,#2f2d2a)" role="img" aria-label="Photo of the open coworking floor with desks, sofas and lockers"></div>
      <div class="photo" style="left:55px;top:210px;width:151px;height:95px;background:linear-gradient(160deg,#d9c49a,#8a6d3e 55%,#3a2d1c)" role="img" aria-label="Photo of the conference room table"></div>
      <div class="photo" style="left:219px;top:210px;width:151px;height:95px;background:linear-gradient(160deg,#dfe3e8,#6c7078 50%,#2a2a2a)" role="img" aria-label="Photo of private desks with black and yellow chairs"></div>
    </section>

    <h3 class="cta-title"><b>Get A Free Day</b><br>To Try Us Out!</h3>
    <div class="rule" style="left:391px;top:758px;width:43px"></div>
    <p class="cta-text">Contact us. We’ll call you back with a “smart lock” code and you’re in!<br>After you try us out, and we talk, you can make your first monthly payment.</p>
    <div class="btn-yellow" style="left:391px;top:828px;width:86px;height:20px;line-height:20px">Contact Us</div>

    <footer class="footer">
      <div class="f-brand"><b>DESKHAVEN</b><br>COSPACE</div>
      <div class="f-tag">Port Halden’s first shared business<br>co-working space</div>
      <div class="f-copy">©2020 Deskhaven. All Rights Reserved.<br><span>Terms of Use | Privacy Policy</span></div>

      <div class="f-head" style="left:234px">Menu</div>
      <ul class="f-list" style="left:232px">
        <li class="hl">Home</li><li>About</li><li>Amenities</li><li>Membership</li><li>Contact</li>
      </ul>
      <div class="f-head" style="left:347px">Social</div>
      <ul class="f-list" style="left:345px">
        <li>Circlely</li><li>ProLinker</li><li>PicStream</li>
      </ul>
      <div class="f-head" style="left:459px">Contact</div>
      <ul class="f-list" style="left:457px">
        <li>418 Harbor St.</li><li>Ste. 210</li><li>Port Halden, TX 75810</li><li>555-201-0148</li><li class="hl">hello@deskhavenmail.com</li>
      </ul>
    </footer>
  </div>

  <svg class="abs" style="left:617px;top:641px" width="108" height="18" viewBox="0 0 108 18">
    <line x1="0" y1="9" x2="90" y2="9" stroke="#850000" stroke-width="2"/>
    <path d="M76 2 L106 9 L76 16 L84 9 Z" fill="#850000"/>
  </svg>

  <div class="portal">
    <div class="portal-title">PAYNEST PAYMENT PORTAL</div>
    <div class="hair" style="left:736px;top:188px;width:464px"></div>

    <div class="pay-btn">QuickPay</div>

    <div class="hair" style="left:754px;top:305px;width:140px;background:#ddd"></div>
    <div class="hair" style="left:1030px;top:305px;width:140px;background:#ddd"></div>
    <div class="or">Or pay with card</div>

    <div class="label" style="top:351px">Email</div>
    <div class="box" style="top:374px;height:41px">
      <div class="cell fill" style="left:0;top:0;width:417px;border:0">h.marsh72@inboxly.test</div>
    </div>

    <div class="label" style="top:434px">Card information</div>
    <div class="box" style="top:458px;height:82px">
      <div class="cell" style="left:0;top:0;width:417px;background:#fff">4242 4242 4242 4242<span class="card-tag">CARDCO</span></div>
      <div class="cell fill" style="left:0;top:40px;width:208px;border-bottom:0;border-right:1px solid var(--border)">08 / 21</div>
      <div class="cell" style="left:208px;top:40px;width:209px;border-bottom:0;background:#fff">123
        <svg class="chev" style="top:12px" width="26" height="17" viewBox="0 0 26 17"><rect x="1" y="3" width="22" height="13" rx="2" fill="#e8e8e8" stroke="#ccc"/><rect x="1" y="6" width="22" height="2.5" fill="#bbb"/><circle cx="20" cy="5" r="4.5" fill="#777"/></svg>
      </div>
    </div>

    <div class="label" style="top:556px">Name on card</div>
    <div class="box" style="top:580px;height:41px">
      <div class="cell fill" style="left:0;top:0;width:417px;border:0">Helena Marsh</div>
    </div>

    <div class="label" style="top:640px">Billing address</div>
    <div class="box" style="top:663px;height:202px;background:var(--field)">
      <div class="cell fill" style="left:0;top:0;width:417px">United States
        <svg class="chev" width="13" height="9" viewBox="0 0 13 9"><path d="M1 1.5l5.5 5.5 5.5-5.5" stroke="#333" stroke-width="2" fill="none"/></svg></div>
      <div class="cell fill" style="left:0;top:40px;width:417px">2710 W Cedar Ln<span class="aside">Clear</span></div>
      <div class="cell fill" style="left:0;top:80px;width:417px">Apt# 402</div>
      <div class="cell fill" style="left:0;top:120px;width:208px;border-right:1px solid var(--border)">Mesa</div>
      <div class="cell fill" style="left:208px;top:120px;width:209px">85201</div>
      <div class="cell fill" style="left:0;top:160px;width:417px;border-bottom:0">Arizona
        <svg class="chev" width="13" height="9" viewBox="0 0 13 9"><path d="M1 1.5l5.5 5.5 5.5-5.5" stroke="#333" stroke-width="2" fill="none"/></svg></div>
    </div>

    <div class="subscribe">Subscribe
      <svg class="abs" style="right:18px;top:14px" width="14" height="18" viewBox="0 0 14 18"><path d="M3.5 8V5.5a3.5 3.5 0 017 0V8" stroke="#fff" stroke-width="2" fill="none"/><rect x="1" y="8" width="12" height="9.5" rx="1.5" fill="#fff"/></svg>
    </div>

    <p class="fine">By confirming your subscription, you allow CoSpace Billing to charge your card for this payment and future payments in accordance with their terms.</p>
    <div class="hair" style="left:736px;top:1017px;width:464px"></div>
  </div>

</div>
</body>
</html>
```